Business Card for Professional Photographer

I'm looking for an eye catching modern clean design that compliments my logo/ website fonts & colours.
I specialise in architecture, corporate & commercial photography so I'm marketing to professional clients rather than portrait / wedding clients.

I would prefer to not have a solid black design.

My logo brand guide is as follows :

Main front font. : Reislust
Main font colour : #fff
Slogan front font : Ubuntu Bold
Monogram front font : Venti Medium
Container colour : #fff

I need print ready files in pdf .png & .eps formats.

Included in the files below are some screen grabs as reference to font & colours etc.

```html
<!DOCTYPE html>
<html lang="en">
<head>
<meta charset="utf-8">
<title>Lumen Axis – Business Card</title>
<link rel="stylesheet" href="https://fonts.googleapis.com/css2?family=Ubuntu:wght@300;400;700&family=Roboto:wght@400&family=Barlow+Condensed:wght@600&display=swap">
<style>
  :root {
    --backdrop: #b4b4b4;
    --card-dark: #121417;
    --card-dark-2: #23262a;
    --card-light: #f6f6f4;
    --gold-deep: #a47d3a;
    --gold-mid: #c29a52;
    --gold-light: #dcbc74;
    --ink: #222222;
    --ink-soft: #333333;
  }
  * { margin: 0; padding: 0; box-sizing: border-box; }
  html, body {
    width: 1200px; height: 576px; overflow: hidden;
    background: var(--backdrop);
  }
  .canvas { position: relative; width: 1200px; height: 576px; }

  .card {
    position: absolute; top: 138px;
    width: 484px; height: 293px;
    border-radius: 10px; overflow: hidden;
  }

  /* Front */
  .card-front { left: 82px; background: var(--card-dark); }
  .front-imagery {
    position: absolute; inset: 0;
    background: linear-gradient(135deg, var(--card-dark-2) 0%, var(--card-dark) 55%, #1b1d21 100%);
  }
  .front-brand {
    position: absolute; left: 66px; top: 95px;
    display: flex; align-items: center; gap: 16px;
  }
  .brand-dot {
    width: 58px; height: 58px; border-radius: 50%;
    border: 3px solid var(--gold-mid);
  }
  .brand-name {
    font-family: "Ubuntu", sans-serif; font-weight: 300;
    font-size: 22px; letter-spacing: 3px; color: var(--gold-light);
    line-height: 1;
  }
  .brand-slogan {
    font-family: "Ubuntu", sans-serif; font-weight: 700;
    font-size: 7.5px; letter-spacing: 1.6px; color: var(--gold-mid);
    margin-top: 6px;
  }
  .front-web {
    position: absolute; left: 138px; top: 254px;
    font-family: "Ubuntu", sans-serif; font-weight: 400;
    font-size: 13px; letter-spacing: 2px; color: var(--gold-light);
  }

  /* Back */
  .card-back { left: 602px; background: var(--card-light); }
  .back-brand { position: absolute; left: 26px; top: 28px; }
  .back-brand .brand-name { font-size: 25px; letter-spacing: 4px; color: var(--gold-mid); }
  .back-brand .brand-slogan { font-size: 8.5px; letter-spacing: 2.4px; margin-top: 7px; }

  .gold-band {
    position: absolute; left: 0; right: 0; top: 107px; height: 131px;
    background: linear-gradient(90deg, var(--gold-deep) 0%, var(--gold-light) 55%, var(--gold-mid) 100%);
  }
  .holder { position: absolute; left: 26px; top: 117px; }
  .holder-name {
    font-family: "Barlow Condensed", sans-serif; font-weight: 600;
    font-size: 19px; color: var(--ink); line-height: 1.1;
  }
  .holder-role {
    font-family: "Roboto", sans-serif; font-size: 12px; color: var(--ink);
    margin-top: 3px;
  }
  .contact-list { position: absolute; left: 26px; top: 173px; list-style: none; }
  .contact-item {
    display: flex; align-items: center; gap: 14px; height: 19px;
    font-family: "Roboto", sans-serif; font-size: 12.5px; color: var(--ink);
  }
  .contact-item svg { width: 11px; height: 11px; fill: var(--ink); flex: none; }
  .address {
    position: absolute; left: 26px; top: 256px;
    font-family: "Roboto", sans-serif; font-size: 12.5px; color: var(--ink-soft);
  }
</style>
</head>
<body>
<main class="canvas">

  <section class="card card-front">
    <div class="front-imagery" role="img" aria-label="Darkened collage of architecture and commercial photographs"></div>
    <div class="front-brand">
      <div class="brand-dot"></div>
      <div>
        <div class="brand-name">LUMEN AXIS</div>
        <div class="brand-slogan">Architecture Corporate Commercial</div>
      </div>
    </div>
    <div class="front-web">www.lumenaxis.com.au</div>
  </section>

  <section class="card card-back">
    <div class="back-brand">
      <div class="brand-name">LUMEN AXIS</div>
      <div class="brand-slogan">Architecture Corporate Commercial</div>
    </div>
    <div class="gold-band"></div>
    <div class="holder">
      <div class="holder-name">Marcus Hale</div>
      <div class="holder-role">Photographer</div>
    </div>
    <ul class="contact-list">
      <li class="contact-item">
        <svg viewBox="0 0 12 12"><path d="M1 3c0-1 1-1.8 5-1.8S11 2 11 3v1H8.5V3h-5v1H1zM3 5h6l2 3v3H1V8zM6 6.5a1.3 1.3 0 1 0 0 2.6 1.3 1.3 0 0 0 0-2.6z"/></svg>
        <span>0491570110</span>
      </li>
      <li class="contact-item">
        <svg viewBox="0 0 12 12"><path d="M0 2h12v8H0zM1 3v.4l5 3.3 5-3.3V3zm0 1.6V9h10V4.6L6 8z"/></svg>
        <span>info@lumenaxis.com.au</span>
      </li>
      <li class="contact-item">
        <svg viewBox="0 0 12 12"><path d="M6 0.5a5.5 5.5 0 1 0 0 11 5.5 5.5 0 0 0 0-11zM1.6 5.3h2.2c.1-1.5.4-2.8.9-3.6A4.5 4.5 0 0 0 1.6 5.3zm0 1.4a4.5 4.5 0 0 0 3.1 3.6c-.5-.8-.8-2.1-.9-3.6zm3.6 0c.1 1.9.5 3.4.8 3.8.3-.4.7-1.9.8-3.8zm0-1.4h1.6C6.7 3.4 6.3 1.9 6 1.5c-.3.4-.7 1.9-.8 3.8zm3 0h2.2a4.5 4.5 0 0 0-3.1-3.6c.5.8.8 2.1.9 3.6zm0 1.4c-.1 1.5-.4 2.8-.9 3.6a4.5 4.5 0 0 0 3.1-3.6z"/></svg>
        <span>www.lumenaxis.com.au</span>
      </li>
    </ul>
    <div class="address">24 Harbour Rd Ashwood Vic 3147</div>
  </section>

</main>
</body>
</html>
```